Small Business Broker Business Card Design

A business card design for a small business brokerage, which is a financial service, not unlike real estate brokerage, but for small businesses such as laundromats, pizza shops, restaurants, cleaners etc. The designs should all be simple, more conservative in nature, using the colors and font of the logo. Again, think real estate Brokerage as a business context
Contact Information for Business Card
Name: Glen R. Harlow. Title: Small Business Advisor. Email: g.harlow@bayfieldcapitalworks.example. Mobile: (555) 274-3918. Office: (555) 806-2147. www.bayfieldcapitalworks.example

```html
<!DOCTYPE html>
<html lang="en">
<head>
<meta charset="utf-8">
<title>Bayfield Capital Works – Business Card</title>
<link rel="stylesheet" href="https://fonts.googleapis.com/css2?family=Montserrat:wght@400;500;600;700;800&display=swap">
<style>
  :root{
    --navy:#1d3a6e;
    --navy-deep:#172f5c;
    --green:#86c140;
    --paper:#ffffff;
    --ink:#1b1f2a;
    --backdrop:#2a2a2c;
  }
  *{box-sizing:border-box;margin:0;padding:0}
  html,body{width:1200px;height:900px;overflow:hidden}
  body{background:var(--backdrop);font-family:'Montserrat',Arial,sans-serif;position:relative}

  .card{position:absolute;width:660px;height:377px;overflow:hidden;box-shadow:0 14px 30px rgba(0,0,0,.45)}

  /* back side */
  .card-back{left:80px;top:46px;background:var(--navy)}
  .card-back .texture{position:absolute;inset:0;background:linear-gradient(200deg,#2a4a85 0%,var(--navy) 45%,var(--navy-deep) 100%)}
  .card-back .brand{position:absolute;left:0;right:0;top:150px;text-align:center}
  .brand-row{display:inline-flex;align-items:center;gap:12px}
  .brand-square{width:22px;height:22px;background:var(--green)}
  .card-back .brand-name{color:var(--paper);font-weight:700;font-size:25px;letter-spacing:.5px}
  .card-back .tagline{color:var(--green);font-weight:600;font-size:11px;letter-spacing:2px;margin-top:6px}

  /* front side */
  .card-front{left:460px;top:474px;background:var(--paper)}
  .front-company{position:absolute;left:34px;top:42px;width:360px}
  .front-company .brand-name{color:var(--navy);font-weight:700;font-size:20px;letter-spacing:.3px;white-space:nowrap}
  .front-company .tagline{color:var(--green);font-weight:600;font-size:9.5px;letter-spacing:1.6px;margin-top:4px;white-space:nowrap}

  .accent-tab{position:absolute;right:0;top:34px;width:14px;height:34px;background:var(--green)}
  .person{position:absolute;right:36px;top:36px;text-align:left}
  .person-name{font-weight:800;font-size:23px;color:var(--navy);white-space:nowrap}
  .person-name .surname{color:var(--green)}
  .person-title{font-size:12px;font-weight:500;color:var(--ink);margin-top:1px}

  .emblem-area{position:absolute;right:40px;top:118px;width:200px;height:180px;background:linear-gradient(135deg,#e9eef6,#f2f7ea)}

  .address{position:absolute;left:34px;top:168px;font-size:13px;line-height:1.35;color:var(--ink);font-style:normal}
  .contacts{position:absolute;left:34px;top:226px;list-style:none;font-size:13px;color:var(--ink)}
  .contacts li{display:flex;align-items:center;gap:9px;height:22px;white-space:nowrap}
  .contacts svg{width:13px;height:13px;fill:var(--navy);flex:none}

  .footer-band{position:absolute;left:0;right:0;bottom:0;height:14px;background:var(--navy)}
</style>
</head>
<body>

<section class="card card-back" aria-label="Card back">
  <div class="texture" role="img" aria-label="Subtle tone-on-tone navy background pattern"></div>
  <div class="brand">
    <div class="brand-row">
      <span class="brand-square"></span>
      <span class="brand-name">BAYFIELD CAPITAL WORKS, INC</span>
    </div>
    <div class="tagline">TRUSTED GUIDANCE FOR LOCAL BUSINESS OWNERS</div>
  </div>
</section>

<section class="card card-front" aria-label="Card front">
  <div class="front-company">
    <div class="brand-name">BAYFIELD CAPITAL WORKS, INC</div>
    <div class="tagline">TRUSTED GUIDANCE FOR LOCAL BUSINESS OWNERS</div>
  </div>

  <div class="accent-tab"></div>
  <div class="person">
    <div class="person-name">Glen R. <span class="surname">Harlow</span></div>
    <div class="person-title">Small Business Advisor</div>
  </div>

  <div class="emblem-area" role="img" aria-label="Brand emblem area"></div>

  <address class="address">
    418 Harbor View Rd<br>Millbrook, Florida 34000
  </address>

  <ul class="contacts">
    <li>
      <svg viewBox="0 0 16 16" aria-hidden="true"><path d="M1 6c0-2 3-3 7-3s7 1 7 3v1h-4V5.5H5V7H1z"/><path d="M4 8h8l2 6H2z"/></svg>
      (555) 806-2147
    </li>
    <li>
      <svg viewBox="0 0 16 16" aria-hidden="true"><path d="M3 1l3 0 1 4-2 1c1 2 3 4 5 5l1-2 4 1v3c0 1-1 2-2 2C7 15 1 9 1 3c0-1 1-2 2-2z"/></svg>
      (555) 274-3918
    </li>
    <li>
      <svg viewBox="0 0 16 16" aria-hidden="true"><path d="M1 3h14v10H1z" fill="none" stroke="#1d3a6e" stroke-width="1.6"/><path d="M1 3l7 6 7-6" fill="none" stroke="#1d3a6e" stroke-width="1.6"/></svg>
      g.harlow@bayfieldcapitalworks.example
    </li>
    <li>
      <svg viewBox="0 0 16 16" aria-hidden="true"><circle cx="8" cy="8" r="6.5" fill="none" stroke="#1d3a6e" stroke-width="1.5"/><path d="M1.5 8h13M8 1.5c-3 3-3 10 0 13M8 1.5c3 3 3 10 0 13" fill="none" stroke="#1d3a6e" stroke-width="1.2"/></svg>
      www.bayfieldcapitalworks.example
    </li>
  </ul>

  <div class="footer-band"></div>
</section>

</body>
</html>
```